Elevating our current Business Card Design

We want to elevate our current business card with a new design to look like a zenith 300 company. We are a premium lubricant distributor (oil and grease).
We need 2 versions, version 1 is as per the uploaded a copy of our current business card with the English version.
For our Chinese version we need to use the front to be English in English and have the back of the card designed exactly like the front for all info to be in Chinese.
The design template needs to be such that we can amend the template with adding different information for each person's card.
The background colour of the card can be changed- we just need to clearly see all information on the card and logos.
The QJR and Ember steady logos cannot have any colour or display changes- only use the logos attached.
All logos need to be included and all information from the attached current card

```html
<!DOCTYPE html>
<html lang="en">
<head>
<meta charset="utf-8">
<title>Korvan Business Card – Front and Back</title>
<link href="https://fonts.googleapis.com/css2?family=Open+Sans:wght@400;600;700&family=Exo+2:wght@700&display=swap" rel="stylesheet">
<style>
  :root{
    --stage:#232323;
    --card:#1d1d20;
    --card-edge:#141416;
    --red:#e8262b;
    --orange:#f29a2e;
    --white:#f4f4f4;
    --grey:#9a9a9a;
    --mark-dark:#0c0c0e;
  }
  *{box-sizing:border-box;margin:0;padding:0}
  html,body{width:1200px;height:780px;overflow:hidden;background:var(--stage)}
  body{font-family:"Open Sans",Arial,sans-serif;color:var(--white);position:relative}

  .card{
    position:absolute;top:60px;width:400px;height:660px;
    background:var(--card);border-radius:22px;
    box-shadow:0 0 0 1px var(--card-edge);
  }
  .card--back{left:170px}
  .card--front{left:630px}

  /* Back */
  .back-mark{
    position:absolute;left:0;right:0;top:250px;text-align:center;
    font-family:"Open Sans",Arial,sans-serif;font-weight:700;
    font-size:78px;letter-spacing:2px;color:var(--mark-dark);
  }
  .back-dot{
    position:absolute;left:176px;top:390px;width:48px;height:48px;
    border-radius:50%;background:var(--orange);
  }

  /* Front */
  .brand{
    position:absolute;top:52px;left:0;right:0;
    display:flex;align-items:center;justify-content:center;gap:12px;
  }
  .brand__dot{width:22px;height:22px;border-radius:50%;background:var(--orange)}
  .brand__name{font-weight:700;font-size:46px;letter-spacing:2px;color:var(--red)}

  .person{position:absolute;top:196px;left:0;right:0;text-align:center}
  .person__name{font-family:"Exo 2","Open Sans",sans-serif;font-weight:700;font-size:34px;color:var(--red);line-height:1.1}
  .person__title{font-size:16px;font-weight:600;color:var(--white);margin-top:2px}

  .rule{position:absolute;height:2px;background:var(--red)}
  .icons{
    position:absolute;top:290px;left:0;right:0;
    display:flex;justify-content:center;gap:14px;
  }
  .icon{width:26px;height:26px;border-radius:7px;background:var(--red);transform:rotate(45deg);display:flex;align-items:center;justify-content:center}
  .icon svg{transform:rotate(-45deg)}

  .contacts{position:absolute;top:334px;left:0;right:0;text-align:center;font-size:16px;line-height:24px}
  .address{position:absolute;top:498px;left:0;right:0;text-align:center;font-size:16px;line-height:24px}
  .pin{position:absolute;top:450px;left:187px}

  .certs{position:absolute;top:556px;left:0;right:0;display:flex;align-items:center;justify-content:flex-end;gap:14px;padding-right:34px}
  .partner{font-weight:700;font-size:14px;color:var(--white);margin-right:auto;margin-left:34px}
  .badge{width:32px;height:32px;border-radius:50%;background:var(--orange);box-shadow:0 0 0 4px #5b5b5b}

  .band{
    position:absolute;left:34px;right:34px;bottom:30px;height:40px;
    border:2px solid var(--red);border-radius:4px;display:flex;overflow:hidden;
  }
  .band__own{flex:1;display:flex;align-items:center;gap:8px;padding-left:10px}
  .band__own-name{font-weight:700;font-size:15px;color:var(--red)}
  .band__own-sub{font-size:8px;line-height:9px;color:var(--red);font-weight:600;text-transform:uppercase}
  .band__supplier{background:var(--red);width:150px;display:flex;flex-direction:column;align-items:center;justify-content:center}
  .band__supplier-name{font-weight:700;font-size:17px;color:var(--card);letter-spacing:1px}
  .band__supplier-sub{font-size:7px;font-weight:600;color:var(--card);letter-spacing:1px}
</style>
</head>
<body>

<section class="card card--back" aria-label="Card back">
  <div class="back-mark">KORVAN</div>
  <div class="back-dot"></div>
</section>

<section class="card card--front" aria-label="Card front">
  <div class="brand"><span class="brand__dot"></span><span class="brand__name">KORVAN</span></div>

  <div class="person">
    <div class="person__name">Mara Quint</div>
    <div class="person__title">Administration Executive</div>
  </div>

  <div class="rule" style="top:262px;left:40px;width:92px"></div>
  <div class="rule" style="top:262px;right:40px;width:92px"></div>

  <div class="icons">
    <span class="icon"><svg width="14" height="14" viewBox="0 0 14 14"><path d="M3 1l2.5 2.5-1.5 1.5a8 8 0 0 0 5 5l1.5-1.5L13 11l-2 2C5.5 13 1 8.5 1 3z" fill="#fff"/></svg></span>
    <span class="icon"><svg width="14" height="14" viewBox="0 0 14 14"><rect x="4" y="1" width="6" height="12" rx="1.2" fill="#fff"/></svg></span>
    <span class="icon"><svg width="14" height="14" viewBox="0 0 14 14"><rect x="1" y="3" width="12" height="8" rx="1" fill="#fff"/><path d="M1 3l6 5 6-5" stroke="#e8262b" fill="none"/></svg></span>
    <span class="icon"><svg width="14" height="14" viewBox="0 0 14 14"><circle cx="7" cy="7" r="5.5" fill="#fff"/><path d="M1.5 7h11M7 1.5c-3 3.5-3 7.5 0 11M7 1.5c3 3.5 3 7.5 0 11" stroke="#e8262b" fill="none"/></svg></span>
  </div>

  <div class="contacts">
    <p>1300 404 217 (Phone)</p>
    <p>+61 400 118 263 (Mobile)</p>
    <p>+61 8 9000 4521 (Fax)</p>
    <p>mara.quint@korvanoil.com</p>
    <p>www.korvanoil.com</p>
  </div>

  <div class="rule" style="top:466px;left:40px;width:136px"></div>
  <div class="rule" style="top:466px;right:40px;width:136px"></div>
  <span class="icon pin"><svg width="14" height="14" viewBox="0 0 14 14"><path d="M7 1a4 4 0 0 1 4 4c0 3-4 8-4 8S3 8 3 5a4 4 0 0 1 4-4z" fill="#fff"/><circle cx="7" cy="5" r="1.5" fill="#e8262b"/></svg></span>

  <div class="address">
    <p>14 Harbourline Drive</p>
    <p>Easton, WA 6190</p>
  </div>

  <div class="certs">
    <span class="partner">Ember steady</span>
    <span class="badge"></span>
    <span class="badge"></span>
    <span class="badge"></span>
  </div>

  <div class="band">
    <div class="band__own">
      <span class="band__own-name">KORVAN</span>
      <span class="band__own-sub">Korvan Oil<br>Supply</span>
    </div>
    <div class="band__supplier">
      <span class="band__supplier-name">VELTRANO</span>
      <span class="band__supplier-sub">PREMIUM LUBRICANTS</span>
    </div>
  </div>
</section>

</body>
</html>
```